Weightloss company needs Business Card

We want a business card that is clean and professional, yet portrays that we are a friendly, innovative, and versatile program designed to fit the needs of our clients.
I would like there to be 2 sides, one side having an appointment card, and the other side containing the logo and business information. There can be decorations on both sides. The logo is attached.

Target Market(s)

Men and women 40-60

Industry/Entity Type

Business

Contact Information for Business Card

Font styles to use
Sans Serif

Requirements
Must have
• The logo, space for business information
Nice to have
• The colors in the logo
Should not have
• No pictures of people or food

```html
<!DOCTYPE html>
<html lang="en">
<head>
<meta charset="utf-8">
<title>Uplift Weightloss – Business Card</title>
<link rel="stylesheet" href="https://fonts.googleapis.com/css2?family=Source+Sans+3:ital,wght@0,400;0,600;0,700;1,400&display=swap">
<style>
  :root {
    --brand-red: #d9062b;
    --brand-cyan: #22b6e0;
    --ink: #4a4a4a;
    --paper: #f3f3f2;
    --backdrop: #e4e4e4;
    --rule: #9a9a9a;
  }
  * { box-sizing: border-box; margin: 0; padding: 0; }
  html, body {
    width: 1105px; height: 1200px; overflow: hidden;
    background: var(--backdrop);
    font-family: "Source Sans 3", sans-serif;
  }
  .card {
    position: absolute; left: 180px;
    width: 746px; height: 427px;
    background: var(--paper);
    overflow: hidden;
  }
  .card--front { top: 118px; }
  .card--back { top: 636px; }

  /* Front */
  .brand {
    position: absolute; left: 63px; top: 100px;
    display: flex; align-items: center; gap: 12px;
    color: var(--brand-red); font-weight: 700; font-size: 36px; letter-spacing: -0.3px;
  }
  .brand__dot { width: 22px; height: 22px; border-radius: 50%; background: var(--brand-red); }
  .contact {
    position: absolute; right: 52px; top: 50px;
    text-align: right; color: var(--ink);
  }
  .contact__name { color: var(--brand-red); font-weight: 600; font-size: 28px; line-height: 32px; }
  .contact__role { color: var(--brand-cyan); font-size: 19px; line-height: 22px; }
  .contact__address { margin-top: 30px; font-size: 20px; line-height: 27px; }
  .contact__list { list-style: none; margin-top: 8px; font-size: 20px; line-height: 28.5px; }
  .contact__list li { display: flex; justify-content: flex-end; align-items: center; gap: 12px; }
  .contact__list svg { width: 18px; height: 18px; fill: var(--brand-red); }
  .base-band { position: absolute; left: 0; right: 0; bottom: 0; }
  .base-band__accent { height: 7px; background: var(--brand-cyan); }
  .base-band__gap { height: 3px; background: #ffffff; }
  .base-band__main { height: 22px; background: var(--brand-red); }

  /* Back */
  .appt__title {
    position: absolute; left: 0; right: 0; top: 38px;
    text-align: center; color: var(--brand-red); font-weight: 600; font-size: 29px;
  }
  .field {
    position: absolute; display: flex; align-items: flex-end;
    color: var(--brand-red); font-size: 21px; line-height: 24px;
  }
  .field__line { flex: 1; border-bottom: 2px dotted var(--rule); margin: 0 0 4px 8px; }
  .field--name { left: 41px; right: 56px; top: 104px; }
  .field--date { left: 39px; width: 354px; top: 157px; }
  .field--time { left: 417px; right: 56px; top: 157px; }
  .field__suffix { font-size: 16px; margin-left: 6px; }
  .field--note { left: 41px; right: 56px; top: 263px; }
  .rule--extra { position: absolute; left: 41px; right: 56px; top: 320px; border-bottom: 2px dotted var(--rule); }
  .days {
    position: absolute; left: 43px; right: 56px; top: 220px;
    display: flex; justify-content: space-between; list-style: none;
    color: var(--brand-red); font-size: 19px;
  }
  .days li { display: flex; align-items: center; gap: 8px; }
  .days li::after {
    content: ""; width: 22px; height: 19px; border: 1.5px solid #666; display: block;
  }
  .appt__notice {
    position: absolute; left: 0; right: 0; top: 356px;
    text-align: center; color: var(--ink); font-style: italic; font-size: 15.5px; line-height: 22px;
  }
</style>
</head>
<body>

<section class="card card--front" aria-label="Business card front">
  <div class="brand">
    <span class="brand__name">Uplift Weightloss</span>
    <span class="brand__dot"></span>
  </div>

  <div class="contact">
    <p class="contact__name">DANIEL HART</p>
    <p class="contact__role">CEO/FOUNDER</p>
    <p class="contact__address">2150 Birchwood Road<br>Fairview, Oregon 97024</p>
    <ul class="contact__list">
      <li>503 218 4470
        <svg viewBox="0 0 24 24" aria-label="Phone"><path d="M6.6 10.8a15 15 0 0 0 6.6 6.6l2.2-2.2a1 1 0 0 1 1-.25 11 11 0 0 0 3.6.6 1 1 0 0 1 1 1V20a1 1 0 0 1-1 1A17 17 0 0 1 3 4a1 1 0 0 1 1-1h3.5a1 1 0 0 1 1 1 11 11 0 0 0 .6 3.6 1 1 0 0 1-.25 1Z"/></svg>
      </li>
      <li>503 771 2096
        <svg viewBox="0 0 24 24" aria-label="Mobile"><path d="M7 1h10a2 2 0 0 1 2 2v18a2 2 0 0 1-2 2H7a2 2 0 0 1-2-2V3a2 2 0 0 1 2-2Zm0 3v14h10V4Zm5 15.5a1 1 0 1 0 0 2 1 1 0 0 0 0-2Z"/></svg>
      </li>
      <li>503 218 4471
        <svg viewBox="0 0 24 24" aria-label="Fax"><path d="M6 2h10l2 2v5H6Zm-3 8h18a2 2 0 0 1 2 2v7H1v-7a2 2 0 0 1 2-2Zm3 7v5h12v-5Z"/></svg>
      </li>
      <li>hello@upliftweight.com
        <svg viewBox="0 0 24 24" aria-label="Email"><path d="M2 5h20v14H2Zm2 2v.4l8 5.2 8-5.2V7Z"/></svg>
      </li>
      <li>www.upliftweight.com
        <svg viewBox="0 0 24 24" aria-label="Website"><circle cx="12" cy="12" r="10"/></svg>
      </li>
    </ul>
  </div>

  <div class="base-band" aria-hidden="true">
    <div class="base-band__accent"></div>
    <div class="base-band__gap"></div>
    <div class="base-band__main"></div>
  </div>
</section>

<section class="card card--back" aria-label="Appointment card back">
  <h2 class="appt__title">Next Appointment</h2>

  <div class="field field--name"><span>Name :</span><span class="field__line"></span></div>
  <div class="field field--date"><span>Date :</span><span class="field__line"></span></div>
  <div class="field field--time"><span>Time :</span><span class="field__line"></span><span class="field__suffix">AM/PM</span></div>

  <ul class="days">
    <li>Sun</li><li>Mon</li><li>Tue</li><li>Wed</li><li>Thu</li><li>Fri</li><li>Sat</li>
  </ul>

  <div class="field field--note"><span>Note :</span><span class="field__line"></span></div>
  <div class="rule--extra"></div>

  <p class="appt__notice">Please give me 24 hours notice if you are unable to keep your appointment or<br>a cancellation fee may be charged.</p>
</section>

</body>
</html>
```